Poster of Core Values & Motto

Create our core values poster and motto. Attached are our core values and our Motto. This poster represents both of our companies Pindle Shred & KorvaBin.

Target Market(s)

Our team / employees

Industry/Entity Type

Shredding and Medical Waste

Colors
59FF00
82FF00
B8FF75
E3FFCB
F4FFEA
EB3D1F
EC4F4E
F09395
F8D3D4
FCEDEE

Requirements
Must have
• Include both companies logos

```html
<!DOCTYPE html>
<html lang="en">
<head>
<meta charset="utf-8">
<title>Core Values & Motto — Pindle Shred & KorvaBin</title>
<link rel="stylesheet" href="https://fonts.googleapis.com/css2?family=Poppins:wght@400;700;800;900&display=swap">
<style>
  :root {
    --backdrop: #e9ecef;
    --paper: #ffffff;
    --ink: #231f20;
    --header-green: #1a8a3e;
    --header-mist: #d6e8e8;
    --teamwork: #0d6630;
    --excellence: #1a9dc4;
    --honesty: #fb0d0d;
    --efficient: #f5be10;
    --secure: #b8105e;
    --dependable: #f76614;
    --on-color: #ffffff;
    --brand-green: #1b8a3e;
  }
  html, body {
    margin: 0;
    width: 988px;
    height: 1200px;
    overflow: hidden;
    background: var(--backdrop);
  }
  .poster {
    position: absolute;
    left: 114px;
    top: 29px;
    width: 760px;
    height: 1141px;
    background: var(--paper);
  }
  .poster svg { display: block; width: 100%; height: 100%; }
  .title { font-family: "Poppins", sans-serif; fill: var(--ink); }
  .title-core { font-weight: 800; font-size: 132px; letter-spacing: 22px; }
  .title-values { font-weight: 900; font-size: 182px; letter-spacing: -4px; }
  .segment { stroke: var(--paper); stroke-width: 19; stroke-linejoin: miter; }
  .seg-teamwork { fill: var(--teamwork); }
  .seg-excellence { fill: var(--excellence); }
  .seg-honesty { fill: var(--honesty); }
  .seg-efficient { fill: var(--efficient); }
  .seg-secure { fill: var(--secure); }
  .seg-dependable { fill: var(--dependable); }
  .icon-slot { fill: #000; opacity: 0.08; }
  .value-name { font-family: "Poppins", sans-serif; font-weight: 800; font-size: 40px; letter-spacing: -0.5px; fill: var(--on-color); }
  .value-name.dark { fill: var(--ink); }
  .value-note { font-family: "Poppins", sans-serif; font-weight: 400; font-size: 22.5px; fill: var(--on-color); }
  .value-note.dark { fill: var(--ink); }
  .motto { font-family: "Poppins", sans-serif; fill: var(--ink); text-anchor: middle; }
  .motto-label { font-weight: 700; font-size: 20px; letter-spacing: 4px; }
  .motto-rule { stroke: var(--ink); stroke-width: 2; stroke-dasharray: 6 5; }
  .motto-small { font-weight: 800; font-size: 38px; }
  .motto-mid { font-weight: 900; font-size: 54px; letter-spacing: -1px; }
  .motto-big { font-weight: 900; font-size: 82px; letter-spacing: -2px; }
  .brand { font-family: "Poppins", sans-serif; font-weight: 800; }
  .brand-korvabin { fill: var(--ink); font-size: 44px; }
  .brand-pindle { fill: var(--brand-green); font-size: 40px; }
  .brand-dot { fill: var(--brand-green); }
</style>
</head>
<body>
<main class="poster">
  <svg viewBox="0 0 1105 1659" xmlns="http://www.w3.org/2000/svg">
    <g class="header">
      <path fill="var(--header-green)" d="M230 0 C150 110 60 220 8 355 C150 460 320 500 470 498 C700 496 900 420 1105 338 L1105 0 Z"/>
      <path fill="var(--header-mist)" d="M274 0 C200 100 140 190 97 290 C240 400 420 445 580 443 C780 440 950 380 1105 325 L1105 0 Z"/>
      <text class="title title-core" x="565" y="175" text-anchor="middle">CORE</text>
      <text class="title title-values" x="556" y="323" text-anchor="middle">VALUES</text>
    </g>

    <g class="values-wheel">
      <path class="segment seg-teamwork" d="M552,549 A503,503 0 0 0 116.4,800.5 L331.2,924.5 A255,255 0 0 1 394.9,851.1 L452,878.8 L456.4,815.6 A255,255 0 0 1 552,797 Z"/>
      <path class="segment seg-excellence" d="M987.6,800.5 A503,503 0 0 0 552,549 L552,797 A255,255 0 0 1 647.6,815.6 L652,878.8 L709.1,851.1 A255,255 0 0 1 772.8,924.5 Z"/>
      <path class="segment seg-honesty" d="M987.6,1303.5 A503,503 0 0 0 987.6,800.5 L772.8,924.5 A255,255 0 0 1 804.5,1016.5 L752,1052 L804.5,1087.5 A255,255 0 0 1 772.8,1179.5 Z"/>
      <path class="segment seg-efficient" d="M116.4,800.5 A503,503 0 0 0 116.4,1303.5 L331.2,1179.5 A255,255 0 0 1 299.5,1087.5 L352,1052 L299.5,1016.5 A255,255 0 0 1 331.2,924.5 Z"/>
      <path class="segment seg-secure" d="M116.4,1303.5 A503,503 0 0 0 552,1555 L552,1307 A255,255 0 0 1 456.4,1288.4 L452,1225.2 L394.9,1252.9 A255,255 0 0 1 331.2,1179.5 Z"/>
      <path class="segment seg-dependable" d="M552,1555 A503,503 0 0 0 987.6,1303.5 L772.8,1179.5 A255,255 0 0 1 709.1,1252.9 L652,1225.2 L647.6,1288.4 A255,255 0 0 1 552,1307 Z"/>

      <g role="img" aria-label="Outline icon of two clasped hands"><rect class="icon-slot" x="356" y="585" width="164" height="140" rx="20"/></g>
      <g role="img" aria-label="Outline icon of a cheering person above a gift box"><rect class="icon-slot" x="584" y="583" width="150" height="125" rx="20"/></g>
      <g role="img" aria-label="Outline icon of a raised hand beside a heart"><rect class="icon-slot" x="869" y="887" width="155" height="128" rx="20"/></g>
      <g role="img" aria-label="Outline icon of a clock inside a gear"><rect class="icon-slot" x="104" y="895" width="135" height="132" rx="20"/></g>
      <g role="img" aria-label="Outline icon of a hand holding a shield with a check"><rect class="icon-slot" x="196" y="1267" width="138" height="133" rx="20"/></g>
      <g role="img" aria-label="Outline icon of a person working at a laptop"><rect class="icon-slot" x="709" y="1243" width="125" height="127" rx="20"/></g>

      <g class="value value-teamwork">
        <text class="value-name" x="221" y="733">SYNERGY /</text>
        <text class="value-name" x="221" y="771">TEAMWORK</text>
        <text class="value-note" x="221" y="795">Get it done attitude with</text>
        <text class="value-note" x="221" y="821">humble confidence</text>
      </g>
      <g class="value value-excellence">
        <text class="value-name" x="630" y="745">EXCELLENCE</text>
        <text class="value-note" x="630" y="770">Exceed expectations</text>
        <text class="value-note" x="630" y="796">with a smile</text>
      </g>
      <g class="value value-honesty" text-anchor="middle">
        <text class="value-name" x="931" y="1060">HONESTY</text>
        <text class="value-name" x="931" y="1098">INTEGRITY</text>
        <text class="value-note" x="931" y="1123">Do the right thing</text>
      </g>
      <g class="value value-efficient" text-anchor="middle">
        <text class="value-name dark" x="177" y="1085">EFFICIENT</text>
        <text class="value-note dark" x="177" y="1110">on-time, sense of</text>
        <text class="value-note dark" x="177" y="1136">urgency, always</text>
        <text class="value-note dark" x="177" y="1162">trying to improve</text>
      </g>
      <g class="value value-secure" text-anchor="end">
        <text class="value-name" x="512" y="1367">SAFE AND</text>
        <text class="value-name" x="512" y="1405">SECURE</text>
        <text class="value-note" x="512" y="1431">We are just as secure</text>
        <text class="value-note" x="512" y="1456">as an armored truck</text>
        <text class="value-note" x="512" y="1482">with money</text>
      </g>
      <g class="value value-dependable">
        <text class="value-name" x="609" y="1423">DEPENDABLE</text>
        <text class="value-note" x="609" y="1448">Do what you say</text>
        <text class="value-note" x="609" y="1474">you will do</text>
      </g>
    </g>

    <g class="motto">
      <line class="motto-rule" x1="389" y1="957" x2="504" y2="957"/>
      <line class="motto-rule" x1="602" y1="957" x2="714" y2="957"/>
      <text class="motto motto-label" x="554" y="964">MOTTO</text>
      <text class="motto motto-small" x="552" y="1007">REMIND PEOPLE</text>
      <text class="motto motto-mid" x="552" y="1055">WHAT GREAT</text>
      <text class="motto motto-big" x="548" y="1120">SERVICE</text>
      <text class="motto motto-small" x="552" y="1157">LOOKS LIKE</text>
    </g>

    <g class="brands">
      <text class="brand brand-korvabin" x="60" y="1605">KorvaBin</text>
      <circle class="brand-dot" cx="790" cy="1575" r="34"/>
      <text class="brand brand-pindle" x="842" y="1567">Pindle</text>
      <text class="brand brand-pindle" x="842" y="1612">Shred</text>
    </g>
  </svg>
</main>
</body>
</html>
```